Marcus Delbridge Finance

Need a personal website advertising Equipment Finance,Business Finance,Commercial Finance, Construction Finance, Bridging Finance. Similar websites are www.corvalend.com.au / www.tarmivest.com.au / www.qbr7.com.au /wwwhalvecredit.com.au

Target Market(s)

Business People

Industry/Entity Type

Business

Number of Pages Required

3 page

Font styles to use
Serif
Sans Serif

Requirements
Must have
• All i want is a simple corporate looking website advertising Equipment Finance, Commercial Finance, Construction Finance, Business Finance, Bridging Finance,

```html
<!DOCTYPE html>
<html lang="en">
<head>
<meta charset="utf-8">
<title>Marcus Delbridge Finance</title>
<link href="https://fonts.googleapis.com/css2?family=Montserrat:wght@300;400;500;600;700&display=swap" rel="stylesheet">
<style>
:root{
  --teal-dark:#0d5a78;
  --teal-deep:#0d4f6b;
  --topbar:#0e6b8f;
  --sky:#29a9e1;
  --sky-dark:#1f8fc4;
  --ink:#2b2b2b;
  --muted:#6f6f6f;
  --grey:#e4e4e4;
  --line:#dcdcdc;
  --slate:#3a3f4a;
  --white:#ffffff;
}
*{box-sizing:border-box;margin:0;padding:0}
html,body{width:1200px;height:2812px;overflow:hidden}
body{position:relative;background:var(--white);font-family:"Montserrat",sans-serif;color:var(--ink)}
.abs{position:absolute}

.topbar{left:0;top:0;width:1200px;height:44px;background:var(--topbar);color:var(--white);font-size:13px}
.topbar .links{left:36px;top:14px}
.topbar .phone{left:636px;top:14px}
.topbar .social{right:36px;top:10px;display:flex;gap:6px}
.dot{width:22px;height:22px;border-radius:50%;background:var(--white)}

.header{left:0;top:44px;width:1200px;height:96px}
.brand{left:36px;top:30px;display:flex;align-items:center;gap:14px;font-size:34px;font-weight:400;color:var(--ink)}
.brand .mark{width:34px;height:34px;border-radius:50%;background:var(--ink)}
.search{left:632px;top:22px;width:348px;height:48px;background:var(--grey);border-radius:4px}
.search .btn{right:8px;top:10px;width:28px;height:28px;background:var(--sky);border-radius:4px}
.quote-btn{left:996px;top:20px;width:166px;height:50px;background:var(--sky);color:var(--white);font-size:17px;display:flex;align-items:center;justify-content:center;border-radius:3px}

.nav{left:0;top:140px;width:1200px;height:56px;background:var(--teal-dark);display:flex;padding-left:36px}
.nav a{width:160px;height:56px;display:flex;align-items:center;justify-content:center;color:var(--white);font-size:17px;text-decoration:none;border-right:2px solid #0a4a63}
.nav a:last-child{border-right:none}
.nav a.active{color:#8fd3f1}

.hero{left:36px;top:224px;width:1128px;height:350px;background:linear-gradient(120deg,#cfd3d6 0%,#e8eaec 35%,#b9c0c7 60%,#dfe2e4 100%)}
.hero-title{left:74px;top:298px;width:446px;height:90px;background:var(--teal-deep);color:var(--white);font-size:40px;font-weight:700;display:flex;align-items:center;padding-left:22px}
.hero-btn{left:74px;top:402px;width:194px;height:50px;background:var(--sky);color:var(--white);font-size:18px;display:flex;align-items:center;justify-content:center}
.dots{left:916px;top:516px;display:flex;gap:12px}
.dots span{width:22px;height:22px;background:var(--teal-dark)}
.dots span.on{background:var(--sky)}

.intro{left:0;top:620px;width:1200px;text-align:center;font-size:18px;line-height:28px;color:var(--ink)}
.partners{left:0;top:730px;width:1200px;display:flex;justify-content:center;gap:70px;align-items:center}
.partners span{font-size:36px;font-weight:500;color:var(--teal-dark)}

.card{top:868px;width:372px;height:308px;background:var(--sky);color:var(--white)}
.card .foot{left:0;bottom:0;width:100%;height:82px;background:linear-gradient(#1f8fc4,#2ea6dc);display:flex;align-items:center;padding-left:40px;gap:34px;font-size:17px}
.card .avatar{left:42px;top:-36px;width:124px;height:124px;border-radius:50%;border:5px solid var(--white);background:linear-gradient(#d9c7b7,#8d7a6c)}
.card .q{right:40px;top:30px;font-size:80px;font-weight:700;color:rgba(255,255,255,.5);line-height:1}
.card p{left:40px;top:118px;width:290px;font-size:17px;line-height:21px}
.stars{color:#f5a623;font-size:18px;letter-spacing:1px}

.pager{left:354px;top:1236px;display:flex;align-items:center;gap:18px;font-size:18px;color:var(--ink)}
.pager .all{margin-left:30px;text-decoration:underline}

.options{left:0;top:1328px;width:1200px;height:406px;background:radial-gradient(ellipse at 70% 40%,#4a505c,#2e323b);color:var(--white)}
.options h2{left:36px;top:48px;font-size:32px;font-weight:700}
.tab{left:36px;width:274px;height:54px;display:flex;align-items:center;justify-content:center;font-size:17px;border-radius:2px}
.tab.active{background:var(--white);color:var(--ink)}
.tab.alt{background:var(--sky);color:var(--white)}
.options p{left:356px;top:134px;width:716px;text-align:center;font-size:17px;line-height:34px;font-weight:300}
.specialist{left:828px;top:308px;width:216px;height:36px;border:2px solid var(--white);display:flex;align-items:center;justify-content:center;gap:8px;font-size:13px;font-weight:600}

.mission h2{left:36px;top:1784px;font-size:32px;font-weight:700;color:var(--teal-deep);letter-spacing:1px}
.mission p{left:36px;top:1862px;width:540px;font-size:17px;line-height:34px}
.mission .photo{left:626px;top:1862px;width:536px;height:250px;background:linear-gradient(90deg,#5d6160 0%,#c9c3b8 45%,#e6ded2 70%,#8e8a84 100%)}

.keywords{left:0;top:2262px;width:1200px;height:246px;background:linear-gradient(180deg,#24355a 0%,#4b5f82 45%,#2a3550 100%);color:var(--white)}
.keywords h2{left:36px;top:60px;font-size:32px;font-weight:700}
.tag{height:44px;border:2px solid rgba(255,255,255,.6);display:flex;align-items:center;justify-content:center;font-size:19px;color:var(--white)}

.footer{left:0;top:2508px;width:1200px;height:304px;font-size:13px;color:var(--ink)}
.pay-label{left:36px;top:44px}
.cards{left:40px;top:80px;width:172px;height:48px;border:1px solid var(--line);display:flex;align-items:center;justify-content:center;gap:8px;font-size:11px;font-weight:600;color:var(--teal-deep)}
.contact{left:288px;top:42px;font-size:12px;line-height:19px}
.contact .row{display:flex;gap:14px;margin-bottom:22px}
.fnav{right:36px;top:54px;text-align:right;font-size:12px;line-height:32px}
.fnav span{margin-left:22px}
.fnav .home{color:#9a9a9a}
.rule{left:0;top:200px;width:1200px;height:1px;background:var(--line)}
.legal{left:36px;top:232px;font-size:12px;line-height:28px}
.follow{right:36px;top:238px;display:flex;align-items:center;gap:6px;font-size:12px}
.follow .dot{background:#c8c8c8}
.follow span.lbl{margin-right:12px}
</style>
</head>
<body>

<div class="abs topbar">
  <div class="abs links">E-Book - Downloads Sitemap</div>
  <div class="abs phone">T: 1300 555 014</div>
  <div class="abs social"><span class="dot"></span><span class="dot"></span><span class="dot"></span><span class="dot"></span></div>
</div>

<header class="abs header">
  <div class="abs brand"><span class="mark"></span>Marcus Delbridge Finance</div>
  <div class="abs search"><span class="abs btn"></span></div>
  <div class="abs quote-btn">Quote Now</div>
</header>

<nav class="abs nav">
  <a class="active">Home</a><a>The Business</a><a>Key People</a><a>Products</a><a>Investors</a><a>Contact Us</a><a>Privacy</a>
</nav>

<div class="abs hero" role="img" aria-label="Photo of two business people shaking hands"></div>
<div class="abs hero-title">Competitive rates</div>
<div class="abs hero-btn">Quote Now</div>
<div class="abs dots"><span class="on"></span><span></span><span></span><span></span></div>

<p class="abs intro">We compare loan and insurance products from some of Australia's leading<br>finance and insurance companies, including:</p>
<div class="abs partners"><span>brennlow</span><span>Halvora</span><span>quentis</span><span>ardmark</span></div>

<div class="abs card" style="left:36px">
  <div class="abs avatar" role="img" aria-label="Client portrait"></div>
  <div class="abs q">&ldquo;</div>
  <p class="abs">Penatibus et magnis dis parturient montes, nascetur ridiculus mus.</p>
  <div class="abs foot">Lena R Hart <span class="stars">★★★★★</span></div>
</div>
<div class="abs card" style="left:414px">
  <div class="abs avatar" role="img" aria-label="Client portrait"></div>
  <div class="abs q">&ldquo;</div>
  <p class="abs">Penatibus et magnis dis parturient montes, nascetur ridiculus mus.</p>
  <div class="abs foot">Lena R Hart <span class="stars">★★★★★</span></div>
</div>
<div class="abs card" style="left:792px">
  <div class="abs avatar" role="img" aria-label="Client portrait"></div>
  <div class="abs q">&ldquo;</div>
  <p class="abs">Penatibus et magnis dis parturient montes, nascetur ridiculus mus.</p>
  <div class="abs foot">Lena R Hart <span class="stars">★★★★★</span></div>
</div>

<div class="abs pager">
  <svg width="18" height="36" viewBox="0 0 18 36"><path d="M16 2 2 18l14 16" fill="none" stroke="#2b2b2b" stroke-width="2"/></svg>
  <span>3/64</span>
  <svg width="18" height="36" viewBox="0 0 18 36"><path d="M2 2l14 16L2 34" fill="none" stroke="#2b2b2b" stroke-width="2"/></svg>
  <span class="all">Click Here To View All Testimonials</span>
</div>

<section class="abs options">
  <h2 class="abs">MY Business Finance Options</h2>
  <div class="abs tab active" style="top:124px">Invoice Factoring</div>
  <div class="abs tab alt" style="top:192px">Trade Finance</div>
  <div class="abs tab alt" style="top:260px">Business Loans</div>
  <p class="abs">Access 85% of your existing and new invoice value within 24 hours. Waiting to be paid leaves you without cash in the bank and distracts from your focus to take on new opportunities. Pay bills and wages on time with funding that grows with your turnover and not your credit rating. [Learn more] [Skip &amp; Apply for a quote]</p>
  <div class="abs specialist">
    <svg width="14" height="14" viewBox="0 0 14 14"><circle cx="7" cy="4" r="3.2" fill="#fff"/><path d="M1 14c0-4 3-6 6-6s6 2 6 6z" fill="#fff"/></svg>
    Speak with a specialist
  </div>
</section>

<section class="mission">
  <h2 class="abs">MY MISSION</h2>
  <p class="abs">We aim to provide financial solutions, at turnaround times and levels of efficiency that exceed all other Financial Institutions! We wish to assist individuals and businesses to achieve long term growth and prosperity. We conduct our business in a professional manner and satisfy our client needs.</p>
  <div class="abs photo" role="img" aria-label="Photo of a smiling businesswoman in an office"></div>
</section>

<section class="abs keywords" role="img" aria-label="Background photo of a coastline at dusk">
  <h2 class="abs">MY KEYWORDS</h2>
  <div class="abs tag" style="left:482px;top:56px;width:112px">Finance</div>
  <div class="abs tag" style="left:606px;top:56px;width:244px">Commercial Finance</div>
  <div class="abs tag" style="left:862px;top:56px;width:248px">Construction Finance</div>
  <div class="abs tag" style="left:482px;top:118px;width:216px">Business Finance</div>
  <div class="abs tag" style="left:710px;top:118px;width:240px">Bridging Finance</div>
</section>

<footer class="abs footer">
  <div class="abs pay-label">Payments</div>
  <div class="abs cards"><span>Paywend</span><span>Corvix</span><span>Meridane</span><span>Ambrolt</span></div>
  <div class="abs contact">
    <div class="row">
      <svg width="16" height="22" viewBox="0 0 16 22"><path d="M8 0a8 8 0 0 0-8 8c0 6 8 14 8 14s8-8 8-14a8 8 0 0 0-8-8zm0 11a3 3 0 1 1 0-6 3 3 0 0 1 0 6z" fill="#2b2b2b"/></svg>
      <div>27 Larnach Street,<br>Coral Bay, Queensland, 4218</div>
    </div>
    <div class="row">
      <svg width="20" height="20" viewBox="0 0 20 20"><circle cx="10" cy="10" r="8.5" fill="none" stroke="#2b2b2b" stroke-width="2"/><path d="M10 5v5l3 2" fill="none" stroke="#2b2b2b" stroke-width="2"/></svg>
      <div>Mon – Fri 9:00am – 5:00pm<br>Sat – Sun - Closed</div>
    </div>
  </div>
  <div class="abs fnav">
    <div><span class="home">Home</span><span>The Business</span><span>Key People</span><span>Products</span><span>Investors</span><span>Contact Us</span><span>Privacy</span></div>
    <div>E-Book | Downloads Sitemap &nbsp;|&nbsp; Privacy Policy &nbsp;|&nbsp; Sitemap</div>
  </div>
  <div class="abs rule"></div>
  <div class="abs legal">Secured by SSL<br>© 2017 Marcus Delbridge Finance</div>
  <div class="abs follow"><span class="lbl">Follow Us</span><span class="dot"></span><span class="dot"></span><span class="dot"></span><span class="dot"></span></div>
</footer>

</body>
</html>
```